Business Cards

Need business card design that I can update for new employees and details. Needs to incorporate our logo, be bright and fun (in line with tourism and holidays)
Would like a Map of Western Australia on the front with locations all the caravan parks we own (just purchased Tom Price so please include that as well as others listed on our website).
Target Market(s)
Famillies
Contact Information for Business Card
5 Cards -
Neil Perrow (Director) e: perrow@wattlebay.com.au p: 0491 570 156
Mira Perrow (Director) e: perrow@wattlebay.com.au p: 0491 570 157
Owen Halvey (General Manager) e: halvey@wattlebay.com.au p: 0491 570 158
Helen Halvey (General Manager) e: halvey@wattlebay.com.au p: 0491 570 159
Colin Danby (Training and Operations Manager) - e: danby@wattlebay.com.au p:0491 570 110
Colors
Look and feel

```html
<!DOCTYPE html>
<html lang="en">
<head>
<meta charset="utf-8">
<title>Wattle Bay Tourist Parks – Business Cards</title>
<link rel="stylesheet" href="https://fonts.googleapis.com/css2?family=Libre+Baskerville:wght@400;700&family=Arimo:wght@400&display=swap">
<style>
  :root {
    --stage: #2e2e2f;
    --card-grey: #58585a;
    --card-white: #f4f4f4;
    --teal: #3cbfca;
    --teal-soft: #62c6b4;
    --ink: #5a5a5c;
    --light: #ffffff;
  }
  * { margin: 0; padding: 0; box-sizing: border-box; }
  html, body {
    width: 1200px; height: 886px; overflow: hidden;
    background: var(--stage);
  }
  .canvas { position: relative; width: 1200px; height: 886px; }

  .card {
    position: absolute; width: 560px; height: 320px;
    box-shadow: 0 14px 30px rgba(0,0,0,.45);
    overflow: hidden;
  }

  /* brand lockup */
  .brand { display: flex; align-items: center; gap: 14px; white-space: nowrap; }
  .brand-square { width: 50px; height: 50px; background: var(--teal); flex: none; }
  .brand-name {
    font-family: "Libre Baskerville", serif; font-weight: 400;
    letter-spacing: 2px; text-transform: uppercase; line-height: 1.35;
  }

  /* back card */
  .card-back { left: 60px; top: 70px; background: var(--card-grey); }
  .card-back .brand { position: absolute; left: 50%; top: 100px; transform: translateX(-50%); }
  .card-back .brand-name { color: var(--light); font-size: 21px; }
  .card-back .web {
    position: absolute; left: 0; right: 0; bottom: 64px; text-align: center;
    font-family: "Arimo", sans-serif; font-size: 13px; letter-spacing: 2.5px;
    color: var(--light);
  }

  /* front card */
  .card-front { left: 580px; top: 470px; background: var(--card-white); }
  .front-band {
    position: absolute; left: 0; right: 0; bottom: 0; height: 146px;
    background: var(--card-grey);
  }
  .front-frame {
    position: absolute; inset: 10px; border: 2px solid var(--teal);
  }
  .card-front .brand { position: absolute; left: 40px; top: 100px; }
  .card-front .brand-square { width: 46px; height: 46px; }
  .card-front .brand-name { color: var(--ink); font-size: 18px; }

  .person {
    position: absolute; left: 40px; bottom: 40px;
    font-family: "Libre Baskerville", serif; color: var(--teal);
    text-transform: uppercase; white-space: nowrap;
  }
  .person-name { font-size: 21px; font-weight: 700; letter-spacing: .5px; }
  .person-role { font-size: 14px; margin-top: 4px; color: var(--teal-soft); }

  .contacts {
    position: absolute; right: 34px; top: 190px; list-style: none;
    font-family: "Arimo", sans-serif; font-size: 13px; color: var(--light);
    white-space: nowrap;
  }
  .contacts li { display: flex; align-items: center; gap: 9px; height: 23px; }
  .contact-icon {
    width: 16px; height: 16px; background: var(--teal); flex: none;
    display: flex; align-items: center; justify-content: center;
  }
</style>
</head>
<body>
<main class="canvas">

  <section class="card card-back" aria-label="Card back">
    <div class="brand">
      <span class="brand-square"></span>
      <span class="brand-name">Wattle Bay<br>Tourist Parks</span>
    </div>
    <p class="web">www.wattlebay.com.au</p>
  </section>

  <section class="card card-front" aria-label="Card front">
    <div class="front-band"></div>
    <div class="front-frame"></div>

    <div class="brand">
      <span class="brand-square"></span>
      <span class="brand-name">Wattle Bay<br>Tourist Parks</span>
    </div>

    <ul class="contacts">
      <li>
        <span class="contact-icon">
          <svg width="10" height="10" viewBox="0 0 10 10"><path d="M2 1 L4 3 L3 4 Q4 6 6 7 L7 6 L9 8 L8 9 Q4 9 1 2 Z" fill="#fff"/></svg>
        </span>
        0491 570 156
      </li>
      <li>
        <span class="contact-icon">
          <svg width="10" height="10" viewBox="0 0 10 10"><rect x="1" y="2.5" width="8" height="5.5" fill="none" stroke="#fff" stroke-width="1"/><path d="M1 2.5 L5 6 L9 2.5" fill="none" stroke="#fff" stroke-width="1"/></svg>
        </span>
        perrow@wattlebay.com.au
      </li>
      <li>
        <span class="contact-icon">
          <svg width="10" height="10" viewBox="0 0 10 10"><circle cx="5" cy="5" r="3.8" fill="none" stroke="#fff" stroke-width="1"/><path d="M1.2 5 H8.8 M5 1.2 Q2.8 5 5 8.8 M5 1.2 Q7.2 5 5 8.8" fill="none" stroke="#fff" stroke-width=".8"/></svg>
        </span>
        www.wattlebay.com.au
      </li>
    </ul>

    <div class="person">
      <p class="person-name">Neil Perrow</p>
      <p class="person-role">Director</p>
    </div>
  </section>

</main>
</body>
</html>
```